Custom Mexican Train Dominos Scorecard

My wife and I regularly play Mexican Train dominos with our friends and family and would like to create a series of custom scorecards specific to our various groups that we play with. The idea would be to have them printed on pads or in notebooks that over time will hold a record of all of our games. Searching around on the web, the only "off the shelf" that I see are pretty plain and boring (see attached). We would love something with a fun and playful mid-century graphic feel to it. Can be a single color or more than one. We want to have the player names incorporated into the design, so for the first one the names would be Olive, Walter, Ruby & Oscar. We will want a place to date each card and of course boxes to fill out the score. I have included a few examples of how the scorecard is basically laid out. Can be any size and can be done in landscape or portrait. I think I would just like the title to say "Domino Night" or potentially no title at all with just a fun domino graphic. Thank you!

Requirements
Must have
• Basic score layout
Nice to have
• nothing in particular
Should not have
• nothing in particular

```html
<!DOCTYPE html>
<html lang="en">
<head>
<meta charset="utf-8">
<title>Domino Night Scorecard</title>
<link href="https://fonts.googleapis.com/css2?family=Bungee&family=Limelight&family=Oswald:wght@500&display=swap" rel="stylesheet">
<style>
  :root {
    --night: #2f5a6a;
    --night-deep: #22404d;
    --skyline: #222226;
    --teal: #92d1d6;
    --red: #d1495b;
    --ink: #1f1f22;
    --paper: #ffffff;
    --title-pink: #e05a6e;
  }
  html, body { margin: 0; padding: 0; overflow: hidden; }
  body { width: 884px; height: 1200px; background: var(--paper); position: relative; }
  .header {
    position: absolute; left: 0; top: 0; width: 884px; height: 190px;
    background: linear-gradient(180deg, var(--night-deep) 0%, var(--night) 60%, var(--skyline) 82%, var(--skyline) 100%);
  }
  .title {
    position: absolute; left: 0; top: 22px; width: 884px; margin: 0;
    text-align: center; font-family: "Limelight", serif; font-weight: 400;
    font-size: 64px; letter-spacing: 6px; color: var(--paper); text-transform: uppercase;
  }
  .title .word-one { color: var(--title-pink); }
  .player {
    position: absolute; top: 198px; width: 150px; margin-left: -75px;
    text-align: center; font-family: "Bungee", sans-serif; font-size: 24px;
    color: var(--ink); text-transform: uppercase;
  }
  .sheet { position: absolute; left: 0; top: 0; }
  .row-number { font-family: "Oswald", sans-serif; font-weight: 500; font-size: 19px; fill: var(--ink); }
  .total-label { font-family: "Oswald", sans-serif; font-weight: 500; font-size: 17px; fill: var(--paper); }
</style>
</head>
<body>
  <div class="header" role="img" aria-label="Night city skyline of domino-shaped buildings with antennas, stars and a full moon">
    <h1 class="title"><span class="word-one">Domino</span> Night</h1>
  </div>

  <div class="player" style="left:293px">Olive</div>
  <div class="player" style="left:442px">Walter</div>
  <div class="player" style="left:593px">Ruby</div>
  <div class="player" style="left:750px">Oscar</div>

  <svg class="sheet" width="884" height="1200" viewBox="0 0 884 1200">
    <defs>
      <pattern id="pip" width="8.5" height="8.5" patternUnits="userSpaceOnUse">
        <circle cx="4.25" cy="4.25" r="1.9" fill="var(--ink)"/>
      </pattern>
    </defs>

    <!-- score bands on even rows -->
    <g class="bands" fill="var(--teal)">
      <rect x="60" y="243" width="165" height="53" rx="9"/><polygon points="212,243 824,248 824,287 212,296"/>
      <rect x="60" y="361.6" width="165" height="53" rx="9"/><polygon points="212,361.6 824,366.6 824,405.6 212,414.6"/>
      <rect x="60" y="480.2" width="165" height="53" rx="9"/><polygon points="212,480.2 824,485.2 824,524.2 212,533.2"/>
      <rect x="60" y="635" width="165" height="54.6" rx="9"/><polygon points="212,635 824,640 824,680.6 212,689.6"/>
      <rect x="60" y="756.1" width="165" height="54.6" rx="9"/><polygon points="212,756.1 824,761.1 824,801.7 212,810.7"/>
      <rect x="60" y="877.3" width="165" height="54.6" rx="9"/><polygon points="212,877.3 824,882.3 824,922.9 212,931.9"/>
      <rect x="60" y="998.4" width="165" height="54.6" rx="9"/><polygon points="212,998.4 824,1003.4 824,1044 212,1053"/>
    </g>

    <!-- total labels -->
    <rect x="63" y="596" width="160" height="34" rx="9" fill="var(--red)"/>
    <text class="total-label" x="137" y="620" text-anchor="middle">SUB TOTAL</text>
    <rect x="63" y="1056" width="160" height="36" rx="9" fill="var(--red)"/>
    <text class="total-label" x="140" y="1081" text-anchor="middle">GAME TOTAL</text>

    <!-- score grid -->
    <g class="grid" fill="none" stroke="var(--red)" stroke-width="2">
      <rect x="212" y="234" width="612" height="866"/>
      <line x1="365" y1="234" x2="365" y2="1092"/>
      <line x1="518" y1="234" x2="518" y2="1092"/>
      <line x1="670" y1="234" x2="670" y2="1092"/>
      <line x1="212" y1="596" x2="824" y2="596"/>
      <line x1="212" y1="630" x2="824" y2="630"/>
      <line x1="212" y1="633" x2="824" y2="633"/>
      <line x1="212" y1="1056" x2="824" y2="1056"/>
      <line x1="212" y1="1092" x2="824" y2="1092"/>
    </g>

    <!-- domino tiles -->
    <g class="tiles">
      <g transform="translate(0,269.6)">
        <rect x="66" y="-23" width="92" height="46" rx="6" fill="var(--paper)"/><line x1="112" y1="-20" x2="112" y2="20" stroke="var(--ink)" stroke-width="1.6"/>
        <g transform="translate(72,-12.75)"><rect width="34" height="25.5" fill="url(#pip)"/></g>
        <g transform="translate(118,-12.75)"><rect width="34" height="25.5" fill="url(#pip)"/></g>
      </g>
      <g transform="translate(0,329)">
        <rect x="66" y="-23" width="92" height="46" rx="6" fill="var(--paper)" stroke="var(--ink)" stroke-width="1.6"/><line x1="112" y1="-20" x2="112" y2="20" stroke="var(--ink)" stroke-width="1.6"/>
        <g transform="translate(67.75,-8.5)"><rect width="42.5" height="17" fill="url(#pip)"/></g>
        <g transform="translate(113.75,-8.5)"><rect width="42.5" height="17" fill="url(#pip)"/></g>
        <circle cx="89" cy="0" r="1.9" fill="var(--ink)"/><circle cx="135" cy="0" r="1.9" fill="var(--ink)"/>
      </g>
      <g transform="translate(0,388.3)">
        <rect x="66" y="-23" width="92" height="46" rx="6" fill="var(--paper)"/><line x1="112" y1="-20" x2="112" y2="20" stroke="var(--ink)" stroke-width="1.6"/>
        <g transform="translate(67.75,-8.5)"><rect width="42.5" height="17" fill="url(#pip)"/></g>
        <g transform="translate(113.75,-8.5)"><rect width="42.5" height="17" fill="url(#pip)"/></g>
      </g>
      <g transform="translate(0,447.6)">
        <rect x="66" y="-23" width="92" height="46" rx="6" fill="var(--paper)" stroke="var(--ink)" stroke-width="1.6"/><line x1="112" y1="-20" x2="112" y2="20" stroke="var(--ink)" stroke-width="1.6"/>
        <g transform="translate(76.25,-12.75)"><rect width="25.5" height="25.5" fill="url(#pip)"/></g>
        <g transform="translate(122.25,-12.75)"><rect width="25.5" height="25.5" fill="url(#pip)"/></g>
      </g>
      <g transform="translate(0,506.8)">
        <rect x="66" y="-23" width="92" height="46" rx="6" fill="var(--paper)"/><line x1="112" y1="-20" x2="112" y2="20" stroke="var(--ink)" stroke-width="1.6"/>
        <g transform="translate(72,-8.5)"><rect width="34" height="17" fill="url(#pip)"/></g>
        <g transform="translate(118,-8.5)"><rect width="34" height="17" fill="url(#pip)"/></g>
      </g>
      <g transform="translate(0,566.1)">
        <rect x="66" y="-23" width="92" height="46" rx="6" fill="var(--paper)" stroke="var(--ink)" stroke-width="1.6"/><line x1="112" y1="-20" x2="112" y2="20" stroke="var(--ink)" stroke-width="1.6"/>
        <g transform="translate(76.25,-12.75)"><rect width="25.5" height="8.5" fill="url(#pip)"/><rect y="17" width="25.5" height="8.5" fill="url(#pip)"/></g>
        <g transform="translate(122.25,-12.75)"><rect width="25.5" height="8.5" fill="url(#pip)"/><rect y="17" width="25.5" height="8.5" fill="url(#pip)"/></g>
        <circle cx="89" cy="0" r="1.9" fill="var(--ink)"/><circle cx="135" cy="0" r="1.9" fill="var(--ink)"/>
      </g>
      <g transform="translate(0,662.3)">
        <rect x="66" y="-23" width="92" height="46" rx="6" fill="var(--paper)"/><line x1="112" y1="-20" x2="112" y2="20" stroke="var(--ink)" stroke-width="1.6"/>
        <g transform="translate(76.25,-12.75)"><rect width="25.5" height="8.5" fill="url(#pip)"/><rect y="17" width="25.5" height="8.5" fill="url(#pip)"/></g>
        <g transform="translate(122.25,-12.75)"><rect width="25.5" height="8.5" fill="url(#pip)"/><rect y="17" width="25.5" height="8.5" fill="url(#pip)"/></g>
      </g>
      <g transform="translate(0,722.9)">
        <rect x="66" y="-23" width="92" height="46" rx="6" fill="var(--paper)" stroke="var(--ink)" stroke-width="1.6"/><line x1="112" y1="-20" x2="112" y2="20" stroke="var(--ink)" stroke-width="1.6"/>
        <circle cx="80" cy="-9" r="1.9" fill="var(--ink)"/><circle cx="98" cy="-9" r="1.9" fill="var(--ink)"/><circle cx="89" cy="0" r="1.9" fill="var(--ink)"/><circle cx="80" cy="9" r="1.9" fill="var(--ink)"/><circle cx="98" cy="9" r="1.9" fill="var(--ink)"/>
        <circle cx="126" cy="-9" r="1.9" fill="var(--ink)"/><circle cx="144" cy="-9" r="1.9" fill="var(--ink)"/><circle cx="135" cy="0" r="1.9" fill="var(--ink)"/><circle cx="126" cy="9" r="1.9" fill="var(--ink)"/><circle cx="144" cy="9" r="1.9" fill="var(--ink)"/>
      </g>
      <g transform="translate(0,783.4)">
        <rect x="66" y="-23" width="92" height="46" rx="6" fill="var(--paper)"/><line x1="112" y1="-20" x2="112" y2="20" stroke="var(--ink)" stroke-width="1.6"/>
        <circle cx="79" cy="-9" r="1.9" fill="var(--ink)"/><circle cx="99" cy="-9" r="1.9" fill="var(--ink)"/><circle cx="79" cy="9" r="1.9" fill="var(--ink)"/><circle cx="99" cy="9" r="1.9" fill="var(--ink)"/>
        <circle cx="125" cy="-9" r="1.9" fill="var(--ink)"/><circle cx="145" cy="-9" r="1.9" fill="var(--ink)"/><circle cx="125" cy="9" r="1.9" fill="var(--ink)"/><circle cx="145" cy="9" r="1.9" fill="var(--ink)"/>
      </g>
      <g transform="translate(0,844)">
        <rect x="66" y="-23" width="92" height="46" rx="6" fill="var(--paper)" stroke="var(--ink)" stroke-width="1.6"/><line x1="112" y1="-20" x2="112" y2="20" stroke="var(--ink)" stroke-width="1.6"/>
        <circle cx="79" cy="-9" r="1.9" fill="var(--ink)"/><circle cx="89" cy="0" r="1.9" fill="var(--ink)"/><circle cx="99" cy="9" r="1.9" fill="var(--ink)"/>
        <circle cx="125" cy="-9" r="1.9" fill="var(--ink)"/><circle cx="135" cy="0" r="1.9" fill="var(--ink)"/><circle cx="145" cy="9" r="1.9" fill="var(--ink)"/>
      </g>
      <g transform="translate(0,904.6)">
        <rect x="66" y="-23" width="92" height="46" rx="6" fill="var(--paper)"/><line x1="112" y1="-20" x2="112" y2="20" stroke="var(--ink)" stroke-width="1.6"/>
        <circle cx="76" cy="-11" r="1.9" fill="var(--ink)"/><circle cx="102" cy="11" r="1.9" fill="var(--ink)"/>
        <circle cx="122" cy="-11" r="1.9" fill="var(--ink)"/><circle cx="148" cy="11" r="1.9" fill="var(--ink)"/>
      </g>
      <g transform="translate(0,965.2)">
        <rect x="66" y="-23" width="92" height="46" rx="6" fill="var(--paper)" stroke="var(--ink)" stroke-width="1.6"/><line x1="112" y1="-20" x2="112" y2="20" stroke="var(--ink)" stroke-width="1.6"/>
        <circle cx="89" cy="0" r="2.2" fill="var(--ink)"/><circle cx="135" cy="0" r="2.2" fill="var(--ink)"/>
      </g>
      <g transform="translate(0,1025.7)">
        <rect x="66" y="-23" width="92" height="46" rx="6" fill="var(--paper)"/><line x1="112" y1="-20" x2="112" y2="20" stroke="var(--ink)" stroke-width="1.6"/>
      </g>
    </g>

    <!-- row values -->
    <g class="row-values">
      <circle cx="190" cy="269.6" r="16" fill="var(--paper)"/><text class="row-number" x="190" y="276.6" text-anchor="middle">12</text>
      <text class="row-number" x="190" y="336" text-anchor="middle">11</text>
      <circle cx="190" cy="388.3" r="16" fill="var(--paper)"/><text class="row-number" x="190" y="395.3" text-anchor="middle">10</text>
      <text class="row-number" x="190" y="454.6" text-anchor="middle">9</text>
      <circle cx="190" cy="506.8" r="16" fill="var(--paper)"/><text class="row-number" x="190" y="513.8" text-anchor="middle">8</text>
      <text class="row-number" x="190" y="573.1" text-anchor="middle">7</text>
      <circle cx="190" cy="662.3" r="16" fill="var(--paper)"/><text class="row-number" x="190" y="669.3" text-anchor="middle">6</text>
      <text class="row-number" x="190" y="729.9" text-anchor="middle">5</text>
      <circle cx="190" cy="783.4" r="16" fill="var(--paper)"/><text class="row-number" x="190" y="790.4" text-anchor="middle">4</text>
      <text class="row-number" x="190" y="851" text-anchor="middle">3</text>
      <circle cx="190" cy="904.6" r="16" fill="var(--paper)"/><text class="row-number" x="190" y="911.6" text-anchor="middle">2</text>
      <text class="row-number" x="190" y="972.2" text-anchor="middle">1</text>
      <circle cx="190" cy="1025.7" r="16" fill="var(--paper)"/><text class="row-number" x="190" y="1032.7" text-anchor="middle">0</text>
    </g>
  </svg>
</body>
</html>
```